NEW Modern Sleek Business Card for VR Language Startup

Our startup is using VR to lead the next wave of world language education. We need a two-sided business card that introduces the larger organization (Brightloom Language Inc) and our contact info on one side and shows the product, Glimwoorld, on the other side.

Side 1 (contact info)= Brightloom Logo and Contact info (name, title, phone, email)

Side 2 (product)= Glimworld logo, text, and website
Text= Culturally Immersive Language Learning Games
Website= www.glimworld-play.com

Target Market(s)

Education, Technology

Contact Information for Business Card

Contact info will be updated upon approval of the design. For now, put this as a placeholder.

Perry Dunmore
Founder & CEO
pdunmore@quillpost-mail.net
(555)-014-2286

Font styles to use
Other font styles liked:
• Gibson and Century Gothic are the brand fonts

Requirements
Nice to have
• I would love to see cohesion between the design and colors of the two logos. I have attached a few business card designs that I like, so you can get a feel for my preferred style.

```html
<!DOCTYPE html>
<html lang="en">
<head>
<meta charset="utf-8">
<title>Brightloom Language – Business Card</title>
<link href="https://fonts.googleapis.com/css2?family=Montserrat:wght@400;500;600;700&family=Questrial&display=swap" rel="stylesheet">
<style>
  :root {
    --page-bg: #e9eaec;
    --card-bg: #ffffff;
    --ink: #1f1f22;
    --ink-soft: #55565c;
    --sky: #2ec6f2;
    --violet: #6a5fc9;
    --link-blue: #2aa3e6;
    --coral: #f0474f;
    --orange: #f7943a;
    --magenta: #b2469e;
    --card-shadow: 0 18px 40px rgba(20, 22, 30, 0.18);
  }
  * { box-sizing: border-box; margin: 0; padding: 0; }
  html, body {
    width: 1200px; height: 900px; overflow: hidden;
    background: var(--page-bg);
    font-family: "Montserrat", "Questrial", sans-serif;
    color: var(--ink);
  }
  .canvas { position: relative; width: 1200px; height: 900px; }
  .card {
    position: absolute; left: 250px; width: 700px; height: 400px;
    background: var(--card-bg);
    box-shadow: var(--card-shadow);
    overflow: hidden;
  }
  .card--product { top: 40px; }
  .card--contact { top: 460px; }

  .card__art {
    position: absolute; left: 0; top: 40px; width: 390px; height: 360px;
  }
  .card--contact .card__art { top: 50px; height: 350px; }

  .product-logo {
    position: absolute; right: 48px; top: 44px;
    font-family: "Questrial", sans-serif;
    font-size: 44px; letter-spacing: 0.5px;
    color: var(--violet);
  }
  .product-copy {
    position: absolute; right: 48px; bottom: 64px; text-align: right;
  }
  .product-copy__tagline {
    font-size: 17px; font-weight: 500; line-height: 1.35; color: var(--ink-soft);
  }
  .product-copy__url {
    margin-top: 12px; font-size: 17px; font-weight: 600; color: var(--link-blue);
  }

  .company-logo {
    position: absolute; right: 48px; top: 48px;
    font-family: "Questrial", sans-serif;
    font-size: 38px; letter-spacing: 6px; text-transform: uppercase;
    color: var(--ink);
  }
  .contact {
    position: absolute; left: 420px; top: 180px; width: 260px;
  }
  .contact__name {
    font-size: 23px; font-weight: 700; letter-spacing: 0.5px; text-transform: uppercase;
    white-space: nowrap;
    background: linear-gradient(90deg, var(--orange), var(--coral) 45%, var(--magenta) 70%, var(--sky));
    -webkit-background-clip: text; background-clip: text; color: transparent;
  }
  .contact__title {
    margin-top: 2px; font-size: 18px; font-weight: 500; color: var(--ink);
  }
  .contact__list { list-style: none; margin-top: 20px; }
  .contact__item {
    display: flex; align-items: center; gap: 8px;
    font-size: 16px; font-weight: 500; line-height: 1.6; white-space: nowrap;
  }
  .contact__item--email { font-size: 14px; }
  .contact__icon { width: 16px; height: 16px; flex: none; }
</style>
</head>
<body>
<main class="canvas">

  <section class="card card--product" aria-label="Product side">
    <svg class="card__art" viewBox="0 0 390 360" role="img" aria-label="Illustration of a head in profile with circuit lines, blue to violet">
      <defs>
        <linearGradient id="artCool" x1="0" y1="0" x2="1" y2="1">
          <stop offset="0" stop-color="var(--sky)"/>
          <stop offset="1" stop-color="var(--violet)"/>
        </linearGradient>
      </defs>
      <path d="M-10 40 C50 10 170 -10 255 20 C340 50 380 160 365 250 C350 330 265 360 160 360 L-10 360 Z" fill="url(#artCool)"/>
    </svg>
    <div class="product-logo">Glimworld</div>
    <div class="product-copy">
      <p class="product-copy__tagline">Culturally Immersive<br>Language Learning Games</p>
      <p class="product-copy__url">www.glimworld-play.com</p>
    </div>
  </section>

  <section class="card card--contact" aria-label="Contact side">
    <svg class="card__art" viewBox="0 0 390 350" role="img" aria-label="Illustration of a head in profile with circuit lines, orange to pink to blue">
      <defs>
        <linearGradient id="artWarm" x1="0" y1="0" x2="0.7" y2="1">
          <stop offset="0" stop-color="var(--orange)"/>
          <stop offset="0.35" stop-color="var(--coral)"/>
          <stop offset="0.65" stop-color="var(--violet)"/>
          <stop offset="1" stop-color="var(--sky)"/>
        </linearGradient>
      </defs>
      <path d="M-10 40 C50 10 170 -10 255 20 C340 50 380 160 365 250 C350 330 265 350 160 350 L-10 350 Z" fill="url(#artWarm)"/>
    </svg>
    <div class="company-logo">Brightloom</div>
    <div class="contact">
      <p class="contact__name">Perry Dunmore</p>
      <p class="contact__title">Founder &amp; CEO</p>
      <ul class="contact__list">
        <li class="contact__item">
          <svg class="contact__icon" viewBox="0 0 24 24" aria-hidden="true"><path fill="var(--coral)" d="M6.6 10.8a15.1 15.1 0 0 0 6.6 6.6l2.2-2.2c.3-.3.7-.4 1-.2 1.1.4 2.3.6 3.6.6.6 0 1 .4 1 1V20c0 .6-.4 1-1 1A17 17 0 0 1 3 4c0-.6.4-1 1-1h3.5c.6 0 1 .4 1 1 0 1.3.2 2.5.6 3.6.1.3 0 .7-.2 1z"/></svg>
          (555)-014-2286
        </li>
        <li class="contact__item contact__item--email">
          <svg class="contact__icon" viewBox="0 0 24 24" aria-hidden="true"><rect x="2" y="5" width="20" height="14" rx="2" fill="var(--magenta)"/><path d="M3 6.5l9 6.5 9-6.5" fill="none" stroke="#fff" stroke-width="1.6"/></svg>
          pdunmore@quillpost-mail.net
        </li>
      </ul>
    </div>
  </section>

</main>
</body>
</html>
```